Stage Design Company Business Card

We are looking to step up up our business card design for our team.

We are a Full service Design and Consultation company for Stage and TV with an emphasis in Theatrical Lighting.

We like our materials to be clean and modern with solid colors free of patterns and gradients. Our brand consists of 4 primary colors Purple, Black, Grey, and White. Provided is our Word Mark as well as our Symbol Logo.

We would like our cards to leave an impression beyond the information, show our attention to design and detail, and make our marks an easily recognized feature (together or apart) for our clients.

We need a warm approachable comfortable feel for some clients, and a professional flair for the board member type clients.

Attached are our brand elements, and our existing cards to give a sense of our style and a glipse at the information we provide on our cards.

Target Market(s)

broad client base from church leaders to high school teachers and architects.

Industry/Entity Type

Business

Contact Information for Business Card

We format our phone number with periods not parenthesis or dashes. Information will be edited for each of our team members, and team member specific cards are not part of this scope, but rather a template so to speak.

Font styles to use
Sans Serif

Colors
6b449b
ffffff
000000
333333
aaaaaa

Requirements
Must have
• Wordmark and logo mark present (does not need to exist on the same side of card)
• Brand Colors,
• Name, Phone, Email, Address.
• Unique choices that make someone stop and take a second look
Nice to have
• It would be nice to somehow convey what we DO, as our brand name does not lend itself to this, outside of an obvious tagline though.....
• social media if not crowded. all of our handles match (instagram, twitter, facebook)
Should not have
• "clipart"

```html
<!DOCTYPE html>
<html lang="en">
<head>
<meta charset="utf-8">
<title>Orvale Business Card</title>
<link rel="stylesheet" href="https://fonts.googleapis.com/css2?family=Source+Sans+3:wght@400;600;700&display=swap">
<style>
  :root {
    --stage-top: #5b5b5b;
    --stage-bottom: #727272;
    --brand-purple: #38216a;
    --brand-purple-text: #3b2170;
    --paper: #ffffff;
    --ink-grey: #555555;
    --mark-light: #d8d6de;
    --decor-purple: #3f2775;
  }
  * { margin: 0; padding: 0; box-sizing: border-box; }
  html, body { width: 1200px; height: 900px; overflow: hidden; }
  body {
    position: relative;
    background: linear-gradient(180deg, var(--stage-top), var(--stage-bottom));
    font-family: "Source Sans 3", sans-serif;
  }
  .card {
    position: absolute;
    top: 306px;
    width: 440px;
    height: 271px;
    border-radius: 11px;
    overflow: hidden;
    box-shadow: 0 2px 6px rgba(0,0,0,0.25);
  }
  .card-front { left: 149px; background: var(--paper); }
  .card-back { left: 608px; background: var(--brand-purple); }

  .front-band {
    position: absolute; left: 0; top: 127px; width: 100%; height: 144px;
    background: var(--brand-purple);
  }
  .wordmark {
    position: absolute;
    font-weight: 600;
    text-transform: uppercase;
    white-space: nowrap;
  }
  .card-front .wordmark {
    left: 31px; top: 38px;
    font-size: 31px; letter-spacing: 0.55em;
    color: var(--brand-purple-text);
  }
  .person {
    position: absolute; right: 22px; top: 44px; text-align: right;
  }
  .person-name {
    font-size: 14px; font-weight: 700; color: var(--brand-purple-text);
    text-transform: uppercase; line-height: 18px;
  }
  .person-title { font-size: 13px; color: var(--ink-grey); line-height: 16px; }

  .contact-list {
    position: absolute; left: 23px; top: 152px; list-style: none;
    color: var(--paper); font-size: 13px; line-height: 16px;
  }
  .contact-list li { display: flex; align-items: center; gap: 5px; }
  .contact-list svg { width: 9px; height: 9px; flex: none; }
  .address {
    position: absolute; left: 23px; top: 211px;
    color: var(--paper); font-size: 13px; line-height: 16px; font-style: normal;
  }
  .front-decor {
    position: absolute; left: 308px; top: 134px; width: 90px; height: 126px;
    border-radius: 45px; background: var(--decor-purple);
  }

  .back-decor {
    position: absolute; inset: 0; background: var(--decor-purple); opacity: 0.5;
  }
  .back-dot {
    position: absolute; left: 78px; top: 107px; width: 58px; height: 58px;
    border-radius: 50%; background: var(--mark-light);
  }
  .card-back .wordmark {
    left: 176px; top: 116px;
    font-size: 33px; letter-spacing: 0.5em;
    color: var(--mark-light);
  }
</style>
</head>
<body>
  <section class="card card-front" aria-label="Card front">
    <div class="front-band"></div>
    <div class="front-decor" role="img" aria-label="Faint brand symbol decoration"></div>
    <div class="wordmark">Orvale</div>
    <div class="person">
      <p class="person-name">Marcus Hale</p>
      <p class="person-title">Managing Director</p>
    </div>
    <ul class="contact-list">
      <li>
        <svg viewBox="0 0 10 10" aria-hidden="true"><path fill="#fff" d="M2 0.5 L3.6 2.6 L2.7 3.6 Q3.8 6 6.4 7.3 L7.4 6.4 L9.5 8 L8.3 9.5 Q1 8.5 0.5 1.7 Z"/></svg>
        044.555.0182
      </li>
      <li>
        <svg viewBox="0 0 10 10" aria-hidden="true"><rect x="0.5" y="2" width="9" height="6.5" fill="#fff"/><path d="M0.8 2.3 L5 5.6 L9.2 2.3" fill="none" stroke="#38216a" stroke-width="0.9"/></svg>
        hello@orvalestage.com
      </li>
      <li>
        <svg viewBox="0 0 10 10" aria-hidden="true"><circle cx="5" cy="5" r="4.5" fill="#fff"/><path d="M5 0.5 V9.5 M0.5 5 H9.5" stroke="#38216a" stroke-width="0.7"/></svg>
        www.orvalestage.com
      </li>
    </ul>
    <address class="address">18 Lantern Row,<br>Northfield, 40211</address>
  </section>

  <section class="card card-back" aria-label="Card back">
    <div class="back-decor" role="img" aria-label="Repeating brand symbol pattern"></div>
    <div class="back-dot"></div>
    <div class="wordmark">Orvale</div>
  </section>
</body>
</html>
```